Personal Blog

The wordpress blog style and layout should be similar to http://www.samfenwick.com

homepage: my photo, list of things, call to action then 3 boxes (The Blog, The Book and podcast)

Other pages: About us, Blog, Consulting, Contact

Target Market(s)

Web Marketing Consultant

Industry/Entity Type

Consulting

Colors
3277b5
33a6d7
f04a50
f68e4e
33b7a4

```html
<!DOCTYPE html>
<html lang="en">
<head>
<meta charset="utf-8">
<title>Karim Belhadi – Personal Blog</title>
<link href="https://fonts.googleapis.com/css2?family=Dosis:wght@500;600;700&family=Arimo:wght@400;700&display=swap" rel="stylesheet">
<style>
:root{
  --teal:#2fb5a0;
  --teal-dark:#259886;
  --dark:#454545;
  --dark-stripe:#4d4d4d;
  --ink:#222;
  --text:#333;
  --muted:#777;
  --line:#d6d6d6;
  --paper:#fff;
  --hero:#f1f4f6;
  --icon-grey:#d4d4d4;
}
*{box-sizing:border-box;margin:0;padding:0}
html,body{width:712px;height:1200px;overflow:hidden}
body{position:relative;background:var(--paper);font-family:Arimo,Arial,sans-serif;color:var(--text)}
.abs{position:absolute}
.striped{background:repeating-linear-gradient(90deg,var(--dark) 0 2px,var(--dark-stripe) 2px 4px)}

/* header */
.site-header{left:0;top:0;width:712px;height:86px}
.brand{left:28px;top:22px;display:flex;align-items:center;font-family:Dosis,sans-serif;font-weight:600;font-size:24px;color:#fff}
.brand-first{background:var(--teal);padding:4px 10px 6px;border-radius:3px;margin-right:6px}
.main-nav{left:308px;top:34px;display:flex;gap:16px;font-family:Dosis,sans-serif;font-weight:600;font-size:14px;color:#fff;letter-spacing:.2px}
.main-nav .current{color:var(--teal)}

/* hero */
.hero{left:0;top:86px;width:712px;height:210px;background:linear-gradient(#f7f9fa,var(--hero));border-bottom:1px solid var(--line)}
.hero-title{left:33px;top:12px;width:650px;font-family:Dosis,sans-serif;font-weight:500;font-size:24px;line-height:28px;color:var(--ink)}
.hero-title em{font-style:normal;color:var(--teal)}
.topics{left:35px;top:80px;list-style:none;font-size:13px;line-height:24.5px;color:#222}
.topics li::before{content:"›";color:var(--teal);font-weight:700;margin-right:11px;font-size:15px}
.hero-photo{left:365px;top:36px;width:325px;height:172px;background:linear-gradient(90deg,#e3e7ea,#cfd8df 40%,#dde4ec 60%,#b9c3cf)}

/* quote */
.testimonial{left:0;top:296px;width:712px;height:108px}
.quote-mark{font-family:Georgia,serif;font-size:40px;color:#ccc}
.quote-text{left:64px;top:36px;width:590px;font-size:12.5px;line-height:18px;color:#222;text-align:left}
.quote-author{right:62px;top:74px;font-size:10px;color:var(--teal)}

/* feature boxes */
.feature{top:408px;width:209px;height:224px;background:#fff;border:1px solid var(--line);text-align:center}
.feature.active{border:2px solid var(--teal)}
.feature-icon{position:absolute;left:50%;top:22px;transform:translateX(-50%)}
.feature h2{position:absolute;left:0;right:0;top:120px;font-family:Dosis,sans-serif;font-weight:600;font-size:19px;color:var(--ink)}
.feature.active h2{color:var(--teal)}
.feature p{position:absolute;left:18px;right:18px;top:148px;font-size:9px;line-height:12.5px;color:#222}
.pill{display:inline-flex;align-items:center;gap:3px;height:15px;padding:0 9px;border:1px solid #bbb;border-radius:8px;background:#fff;font-size:9px;color:#444}
.pill.solid{background:var(--teal);border-color:var(--teal);color:#fff}
.pill.teal{border-color:var(--teal);color:var(--teal)}
.feature .pill{position:absolute;left:50%;bottom:-8px;transform:translateX(-50%)}

/* recent posts */
.section-rule{left:28px;top:684px;width:656px;height:3px;border-top:1px solid var(--line);border-bottom:1px solid var(--line)}
.section-title{left:300px;top:676px;padding:0 12px;background:#fff;font-weight:700;font-size:12.5px;color:#111}
.post{top:712px;width:152px;height:270px;background:#fff;border:1px solid var(--line)}
.post.active{border-color:var(--teal)}
.post-image{position:absolute;left:4px;top:4px;width:142px;height:112px}
.post h3{position:absolute;left:14px;right:8px;top:126px;font-family:Dosis,sans-serif;font-weight:600;font-size:13.5px;line-height:17px;color:var(--ink)}
.post.active h3{color:var(--teal)}
.post p{position:absolute;left:14px;right:10px;top:181px;font-size:9px;line-height:12px;color:#222}
.post .pill{position:absolute;left:10px;top:228px}
.cam{display:inline-block;vertical-align:middle;margin-left:6px}

/* footer */
.site-footer{left:0;top:1008px;width:712px;height:192px}
.footer-col{top:20px;color:#fff}
.footer-col h4{font-family:Dosis,sans-serif;font-weight:600;font-size:17px;letter-spacing:.3px}
.footer-about p{font-size:9px;line-height:12px;margin-top:10px;width:196px}
.footer-about p+p{margin-top:3px}
.footer-about a{display:block;font-size:9px;color:var(--teal);margin-top:6px;text-decoration:none}
.field{width:200px;height:22px;background:#fff;border-radius:2px;margin-top:9px;font-size:9px;color:#333;padding:5px 8px}
.field:first-of-type{margin-top:12px}
.join-btn{width:200px;height:28px;margin-top:11px;background:var(--teal);border-radius:3px;text-align:center;font-family:Dosis,sans-serif;font-weight:600;font-size:17px;line-height:28px;color:#fff}
.social{display:flex;gap:12px;margin-top:12px}
.social span{width:32px;height:32px;border-radius:4px;background:#8a8a8a}
.social span.active{background:var(--teal)}
.connect{text-align:center;width:170px;font-size:9px;margin-top:12px;line-height:15px}
.connect a{color:var(--teal);text-decoration:none}
.footer-rule{left:28px;top:162px;width:656px;border-top:1px solid #777}
.copyright{left:0;top:174px;width:712px;text-align:center;font-size:9px;color:#fff}
.copyright a{color:var(--teal);text-decoration:none}
</style>
</head>
<body>

<header class="site-header striped abs">
  <div class="brand abs"><span class="brand-first">Karim</span><span>Belhadi</span></div>
  <nav class="main-nav abs">
    <span class="current">ABOUT</span><span>BLOG</span><span>CONSULTING</span><span>RESOURCES</span><span>BOOK</span><span>CONTACT</span>
  </nav>
</header>

<section class="hero abs">
  <h1 class="hero-title abs">Test go here and <em>Product Management,</em> text here <em>Online Marketing,</em> to learn these topics:</h1>
  <ul class="topics abs">
    <li>Product Management</li>
    <li>Customer Development</li>
    <li>Digital Marketing</li>
    <li>Branding &amp; Reputation</li>
    <li>Entreprenership</li>
  </ul>
  <div class="hero-photo abs" role="img" aria-label="Photo of the consultant smiling at his desk beside a computer monitor"></div>
</section>

<section class="testimonial abs">
  <span class="quote-mark abs" style="left:340px;top:-6px">&#8220;</span>
  <span class="quote-mark abs" style="left:34px;top:26px;font-size:30px">&#8220;</span>
  <p class="quote-text abs">"... I was blown away by his breadth of industry knowledge, the straight talking delivery and collaborative format. A highly recommended social media expert and thought leader..."</p>
  <span class="quote-mark abs" style="left:640px;top:52px;font-size:30px">&#8221;</span>
  <span class="quote-author abs">-Marc Delaney - Marketing</span>
</section>

<article class="feature active abs" style="left:27px">
  <svg class="feature-icon" width="90" height="90" viewBox="0 0 90 90">
    <circle cx="45" cy="45" r="44" fill="#fff" stroke="#ddd"/>
    <circle cx="45" cy="45" r="37" fill="var(--teal)"/>
    <g fill="none" stroke="#fff" stroke-width="3">
      <ellipse cx="40" cy="40" rx="15" ry="11"/>
      <ellipse cx="51" cy="50" rx="14" ry="10"/>
    </g>
    <path d="M30 49 l-3 7 l8 -4z M60 57 l4 6 l-9 -3z" fill="#fff"/>
  </svg>
  <h2>The Blog</h2>
  <p>Lorem Ipsum is simply dummy text of the printing &amp; typesetting industry. Lorem Ipsum has been industry's standard dummy text ever since the 1500s.</p>
  <span class="pill solid">Read More &#8853;</span>
</article>

<article class="feature abs" style="left:251px">
  <svg class="feature-icon" width="90" height="90" viewBox="0 0 90 90">
    <circle cx="45" cy="45" r="44" fill="#fff" stroke="#ddd"/>
    <circle cx="45" cy="45" r="37" fill="var(--icon-grey)"/>
    <rect x="34" y="28" width="22" height="32" rx="2" fill="#fff"/>
    <rect x="37" y="28" width="2" height="32" fill="var(--icon-grey)"/>
  </svg>
  <h2>The Book</h2>
  <p>Lorem Ipsum is simply dummy text of the printing &amp; typesetting industry. Lorem Ipsum has been industry's standard dummy text ever since the 1500s.</p>
  <span class="pill">Read More &#8853;</span>
</article>

<article class="feature abs" style="left:475px">
  <svg class="feature-icon" width="90" height="90" viewBox="0 0 90 90">
    <circle cx="45" cy="45" r="44" fill="#fff" stroke="#ddd"/>
    <circle cx="45" cy="45" r="37" fill="var(--icon-grey)"/>
    <circle cx="52" cy="36" r="7" fill="#fff"/>
    <path d="M38 60 q0 -14 14 -14 q14 0 14 14z" fill="#fff"/>
    <circle cx="38" cy="40" r="6" fill="#fff" opacity=".85"/>
    <path d="M26 60 q0 -12 12 -12 q6 0 8 3 q-6 4 -6 9z" fill="#fff" opacity=".85"/>
  </svg>
  <h2>Consulting</h2>
  <p>Lorem Ipsum is simply dummy text of the printing &amp; typesetting industry. Lorem Ipsum has been industry's standard dummy text ever since the 1500s.</p>
  <span class="pill">Read More &#8853;</span>
</article>

<div class="section-rule abs"></div>
<h2 class="section-title abs">RECENT POSTS</h2>

<article class="post active abs" style="left:27px">
  <div class="post-image" role="img" aria-label="Photo of a meeting table with laptops and coffee cups" style="background:linear-gradient(135deg,#8a5a2c,#c68e4f 50%,#5b3a1d)"></div>
  <h3>Yet Another Video Post Format With Embedded Media <svg class="cam" width="11" height="8" viewBox="0 0 11 8"><rect width="7" height="8" rx="1" fill="var(--teal)"/><path d="M7 4 l4 -3 v6z" fill="var(--teal)"/></svg></h3>
  <p>Lorem Ipsum is simply dummy text of the printing &amp; typesetting industry.</p>
  <span class="pill teal">Read More &#8853;</span>
</article>

<article class="post abs" style="left:195px">
  <div class="post-image" role="img" aria-label="Photo of a business team in suits applauding" style="background:linear-gradient(180deg,#f2f2f2,#c9c9c9 55%,#3a3d45)"></div>
  <h3>Yet Another Video Post Format With Embedded Media <svg class="cam" width="11" height="8" viewBox="0 0 11 8"><rect width="7" height="8" rx="1" fill="#222"/><path d="M7 4 l4 -3 v6z" fill="#222"/></svg></h3>
  <p>Lorem Ipsum is simply dummy text of the printing &amp; typesetting industry.</p>
  <span class="pill teal">Read More &#8853;</span>
</article>

<article class="post abs" style="left:363px">
  <div class="post-image" role="img" aria-label="Photo of a hand touching a digital interface screen" style="background:linear-gradient(135deg,#1e2a38,#4d6175 50%,#2a3442)"></div>
  <h3>Yet Another Video Post Format With Embedded Media <svg class="cam" width="11" height="8" viewBox="0 0 11 8"><rect width="7" height="8" rx="1" fill="#222"/><path d="M7 4 l4 -3 v6z" fill="#222"/></svg></h3>
  <p>Lorem Ipsum is simply dummy text of the printing &amp; typesetting industry.</p>
  <span class="pill teal">Read More &#8853;</span>
</article>

<article class="post abs" style="left:531px">
  <div class="post-image" role="img" aria-label="Photo of hands on a desk telephone and keyboard" style="background:linear-gradient(135deg,#dcdcdc,#9a9a9a 55%,#3b3b3b)"></div>
  <h3>Yet Another Video Post Format With Embedded Media <svg class="cam" width="11" height="8" viewBox="0 0 11 8"><rect width="7" height="8" rx="1" fill="#222"/><path d="M7 4 l4 -3 v6z" fill="#222"/></svg></h3>
  <p>Lorem Ipsum is simply dummy text of the printing &amp; typesetting industry.</p>
  <span class="pill teal">Read More &#8853;</span>
</article>

<footer class="site-footer striped abs">
  <div class="footer-col footer-about abs" style="left:28px">
    <h4>ENTREPRENEUR, SPEAKER,</h4>
    <p>Lorem Ipsum is simply dummy text of the printing &amp; typesetting industry. Lorem Ipsum has been industry's standard dummy text ever since the 1500s.</p>
    <p>Lorem Ipsum is simply dummy text of the printing &amp; typesetting industry.</p>
    <a>[ Read the long-winded version! ]</a>
  </div>
  <div class="footer-col abs" style="left:251px">
    <h4>JOIN MY NEW BUSINESS</h4>
    <div class="field">Enter your name...</div>
    <div class="field">Enter your email...</div>
    <div class="join-btn">JOIN FOR FREE!</div>
  </div>
  <div class="footer-col abs" style="left:475px">
    <h4>JOIN MY NEW BUSINESS</h4>
    <div class="social" role="img" aria-label="Social network links">
      <span class="active"></span><span></span><span></span><span></span>
    </div>
    <p class="connect">OR<br>Connect with via <a>email</a></p>
  </div>
  <div class="footer-rule abs"></div>
  <p class="copyright abs">© 2014 K. Belhadi <a>www.karimbelhadi.com</a> | All Right Reserved.</p>
</footer>

</body>
</html>
```